RK Holdings Company brochure

require the design of a brochure for my company RK holdings which incorporates 2 separate companies specialising in home technology and security. Im not sure whether its going to be best to do one brochure with all the info in or 2 individual ones

Target Market(s)

Footballers and High net worth individuals

Industry/Entity Type

Information Technology

Font styles to use
Serif
Other font styles liked:
• Neuropol (this is the logo font)

Colors
ec1f27
000000
9d9d9d

Requirements
Must have
• 2 sections one for audio visual and 1 for security

```html
<!DOCTYPE html>
<html lang="en">
<head>
<meta charset="utf-8">
<title>Northgate Technologies Brochure</title>
<link href="https://fonts.googleapis.com/css2?family=Open+Sans:wght@400;600;700&display=swap" rel="stylesheet">
<style>
:root{
  --red:#ec1f27;
  --black:#000000;
  --grey:#9d9d9d;
  --ink:#3a3a3a;
  --paper:#f4f4f6;
  --stage:#e4e4e4;
}
*{margin:0;padding:0;box-sizing:border-box}
html,body{width:800px;height:1200px;overflow:hidden;background:var(--stage)}
body{font-family:"Open Sans",Arial,sans-serif;color:var(--ink)}
.canvas{position:relative;width:800px;height:1200px}
.spread{position:absolute;left:20px;width:760px;height:537px;overflow:hidden;box-shadow:0 6px 18px rgba(0,0,0,.25)}
.spread--cover{top:20px;background:var(--black)}
.spread--inside{top:623px;background:var(--paper)}
.spread svg.art{position:absolute;inset:0;width:760px;height:537px}
.spine{position:absolute;left:379px;top:0;width:2px;height:537px;background:linear-gradient(90deg,rgba(0,0,0,.18),rgba(255,255,255,.15))}

/* cover */
.about{position:absolute;left:152px;top:38px;width:190px;color:#fff}
.about h2{font-size:12px;font-weight:600;margin-bottom:6px}
.about p{font-size:8.4px;line-height:1.5}
.contact{position:absolute;color:#fff;font-size:9px;line-height:1.4}
.contact svg{width:9px;height:9px;vertical-align:-1px;margin-right:4px}
.contact--address{left:40px;top:452px}
.contact--address .lines{display:inline-block;vertical-align:top}
.contact--phone{left:138px;top:492px}
.contact--email{left:200px;top:455px}
.contact--web{left:560px;top:490px}
.brand{position:absolute;left:582px;top:400px;display:flex;align-items:center;gap:6px}
.brand__dot{width:22px;height:22px;border-radius:50%;background:var(--red)}
.brand__name{color:#fff;font-size:9px;font-weight:600;line-height:1.2;width:110px}

/* inside */
.page-text{position:absolute;top:32px;width:320px}
.page-text--left{left:28px}
.page-text--right{left:412px}
.section-title{color:var(--red);font-size:11.5px;font-weight:600;padding-bottom:2px;border-bottom:1px solid var(--red);display:inline-block;padding-right:40px;margin-bottom:6px}
.body-copy{font-size:6.3px;line-height:1.5;margin-bottom:5px;color:var(--ink)}
.body-copy strong{font-weight:700}
.ticks{list-style:none;margin-bottom:7px}
.ticks li{font-size:6.3px;line-height:1.45;padding-left:10px;position:relative;margin-bottom:2px}
.ticks li::before{content:"";position:absolute;left:1px;top:1px;width:3px;height:5px;border:solid var(--red);border-width:0 1.4px 1.4px 0;transform:rotate(40deg)}
.section-title + .body-copy{margin-top:0}
.block-gap{margin-top:8px}
.web-inside{position:absolute;left:598px;top:506px;color:#fff;font-size:9px}
.web-inside svg{width:9px;height:9px;vertical-align:-1px;margin-right:4px}
</style>
</head>
<body>
<div class="canvas">

  <!-- outer cover spread -->
  <section class="spread spread--cover">
    <svg class="art" viewBox="0 0 760 537" aria-hidden="false">
      <defs>
        <linearGradient id="roomBack" x1="0" y1="0" x2="1" y2="1">
          <stop offset="0" stop-color="#2a1d17"/>
          <stop offset=".5" stop-color="#4a3328"/>
          <stop offset="1" stop-color="#1a1210"/>
        </linearGradient>
        <linearGradient id="roomFront" x1="0" y1="0" x2="0" y2="1">
          <stop offset="0" stop-color="#d9cfc8"/>
          <stop offset=".35" stop-color="#6a3040"/>
          <stop offset="1" stop-color="#8a4a78"/>
        </linearGradient>
      </defs>
      <g role="img" aria-label="Photograph of a dark home cinema room with wall mounted control screen">
        <rect x="0" y="0" width="380" height="440" fill="url(#roomBack)"/>
      </g>
      <g role="img" aria-label="Photograph of a private cinema room with a large screen and purple carpet">
        <rect x="380" y="0" width="380" height="420" fill="url(#roomFront)"/>
      </g>
      <rect x="130" y="0" width="232" height="408" fill="var(--red)" opacity=".86"/>
      <!-- partner badge -->
      <rect x="202" y="312" width="90" height="78" rx="6" fill="#fff"/>
      <rect x="210" y="320" width="74" height="62" rx="4" fill="var(--red)"/>
      <!-- wave -->
      <path d="M0,418 C200,432 420,450 560,382 C650,338 720,300 760,272" fill="none" stroke="#fff" stroke-width="4"/>
      <path d="M0,426 C200,440 420,458 560,390 C650,346 720,308 760,280" fill="none" stroke="var(--red)" stroke-width="10"/>
      <path d="M0,432 C200,446 420,464 560,396 C650,352 720,314 760,286 L760,537 L0,537 Z" fill="var(--black)"/>
    </svg>
    <div class="spine"></div>

    <div class="about">
      <h2>About us</h2>
      <p>With offices in London and Newcastle, we design, install and service entertainment and control systems for our clients. The service is personal, unintimidating and of the highest quality. We create systems that enrich and support our clients' lives, giving them the technology they need without the compromise.</p>
    </div>

    <div class="contact contact--address">
      <svg viewBox="0 0 10 10"><path d="M5 0a3.5 3.5 0 0 0-3.5 3.5C1.5 6 5 10 5 10s3.5-4 3.5-6.5A3.5 3.5 0 0 0 5 0zm0 5a1.4 1.4 0 1 1 0-2.8A1.4 1.4 0 0 1 5 5z" fill="var(--red)"/></svg><span class="lines">Northgate Technologies Ltd<br>Ashby House<br>14-18 Riverside Walk<br>London<br>SE1 9ZZ</span>
    </div>
    <div class="contact contact--phone">
      <svg viewBox="0 0 10 10"><circle cx="5" cy="5" r="4.3" fill="none" stroke="var(--red)" stroke-width="1.2"/><path d="M3.4 2.8l1 1-.5.6c.3.6.8 1.1 1.4 1.4l.6-.5 1 1-.6.8C4.7 7 3 5.3 2.7 3.4z" fill="var(--red)"/></svg>0207 555 0192
    </div>
    <div class="contact contact--email">
      <svg viewBox="0 0 10 10"><rect x=".8" y="2" width="8.4" height="6" fill="none" stroke="var(--red)" stroke-width="1.1"/><path d="M1 2.3l4 3 4-3" fill="none" stroke="var(--red)" stroke-width="1.1"/></svg>info@northgatetech.co.uk
    </div>
    <div class="contact contact--web">
      <svg viewBox="0 0 10 10"><circle cx="5" cy="5" r="4.3" fill="var(--red)"/><path d="M.7 5h8.6M5 .7c-2.2 2.6-2.2 6 0 8.6M5 .7c2.2 2.6 2.2 6 0 8.6" fill="none" stroke="#000" stroke-width=".7"/></svg>www.northgatetech.co.uk
    </div>
    <div class="brand">
      <span class="brand__dot"></span>
      <span class="brand__name">Northgate Protection Solutions</span>
    </div>
  </section>

  <!-- inside spread -->
  <section class="spread spread--inside">
    <svg class="art" viewBox="0 0 760 537">
      <defs>
        <radialGradient id="sheen" cx=".5" cy=".4" r=".7">
          <stop offset="0" stop-color="#ffffff"/>
          <stop offset="1" stop-color="#e2e2e6"/>
        </radialGradient>
      </defs>
      <rect width="760" height="537" fill="url(#sheen)"/>
      <path d="M0,385 C150,412 300,452 400,462 C550,476 680,468 760,452" fill="none" stroke="#cfcfcf" stroke-width="14"/>
      <path d="M0,396 C150,424 300,464 400,474 C550,488 680,480 760,464" fill="none" stroke="var(--red)" stroke-width="7"/>
      <path d="M0,402 C150,430 300,470 400,480 C550,494 680,486 760,470 L760,537 L0,537 Z" fill="var(--black)"/>

      <g role="img" aria-label="Photograph of a remote control and touch panel">
        <circle cx="46" cy="402" r="30" fill="#3a4a66" stroke="var(--red)" stroke-width="4"/>
      </g>
      <g role="img" aria-label="Photograph of a cinema screening room">
        <circle cx="140" cy="432" r="25" fill="#5a3a5a" stroke="var(--red)" stroke-width="4"/>
      </g>
      <g role="img" aria-label="Photograph of a wireless speaker device">
        <circle cx="228" cy="456" r="18" fill="#d8d8dc" stroke="var(--red)" stroke-width="3"/>
      </g>
      <g role="img" aria-label="Photograph of a security keypad">
        <circle cx="482" cy="484" r="24" fill="#4c5564" stroke="var(--red)" stroke-width="4"/>
      </g>
      <g role="img" aria-label="Photograph of a living room interior">
        <circle cx="566" cy="482" r="26" fill="#6b5140" stroke="var(--red)" stroke-width="4"/>
      </g>
      <g role="img" aria-label="Photograph of a smartphone showing a door entry video call">
        <circle cx="680" cy="464" r="34" fill="#c9ccd2" stroke="var(--red)" stroke-width="5"/>
      </g>
    </svg>
    <div class="spine" style="background:linear-gradient(90deg,rgba(0,0,0,.12),rgba(255,255,255,.4))"></div>

    <div class="page-text page-text--left">
      <h3 class="section-title">Audio Visual</h3>
      <p class="body-copy"><strong>Northgate Technologies</strong> provide an extensive range of state-of-the-art video conferencing and audio visual services, combining design, procurement, implementation and support to give a complete end to end service.</p>
      <p class="body-copy">Our highly trained staff provide a focused approach to the design and installation of control, visual and audio systems. Project managers and engineers are highly experienced in a wide range of services involving multi-room, multi-source audio visual systems, lighting and video conferencing, thus providing a complete suite of professionally installed solutions.</p>
      <p class="body-copy">Our services include video conferencing to single user, desktop or multi room environments, integrated audio visual for commercial, home and marine sectors, and control for lighting, blinds and heating from any device, anywhere, over a fully structured data cabling network.</p>
      <p class="body-copy">Our designs combine a simple approach of understanding a client's functional requirements within a space, consideration of the complete IT infrastructure and then matching these needs to a design that gives maximum user experience, intuitive control, sustainability and real value for your investment.</p>
      <h3 class="section-title block-gap">Networks</h3>
      <p class="body-copy">It has always been our belief that whatever technology is being used to run a business, it is completely reliant on the very network platform it sits on.</p>
      <p class="body-copy"><strong>Northgate Technologies</strong> is dedicated in providing customers with the right network platforms to underpin their business requirements and form the core of our solution designs. Whether it is voice, data or video we aim to look further than the immediate requirement to ensure that the solutions we implement now will support the applications of the future.</p>
      <p class="body-copy">Our solutions include the design, installation and support of local area networks for office space, commercial, retail and residential properties, structured cabling, wireless coverage and fibre, providing flexible, efficient and secure services.</p>
    </div>

    <div class="page-text page-text--right">
      <h3 class="section-title">Unified Communications</h3>
      <p class="body-copy">Simplify business processes that depend on human interaction. Northgate Technologies Unified Communications solutions help close the productivity gap created by globalisation.</p>
      <p class="body-copy">By using the intelligence of the network for context and collaboration, your organisation can move with greater speed and agility. Employees, business partners and customers can connect in real time and conduct business across multiple work spaces.</p>
      <p class="body-copy">Our Unified Communications solutions combine all forms of business communications into a single, unified solution for powerful new ways to:</p>
      <ul class="ticks">
        <li>Collaborate across companies and work spaces, connecting employees, partners and vendors.</li>
        <li>Accelerate decision making and customer service cycles with the information people need in real time.</li>
        <li>Innovate across the value chain, embedding communications into work flows and business processes.</li>
        <li>Integrate applications, allowing workers to collaborate in real time using their favourite tools and software.</li>
      </ul>
      <h3 class="section-title">Building Security</h3>
      <p class="body-copy">At <strong>Northgate Technologies</strong> we look after your business by delivering high quality Total Building Security &amp; Management solutions. We are specialists in traditional and IP based access control, CCTV and building management systems, using the latest technology to get the best out of your devices.</p>
      <p class="body-copy">With our group's combined expertise, we can easily integrate with existing or new IT infrastructure or audio visual systems to provide a complete building wide portfolio of services to manage, secure and evolve your building so that it meets legislation, sustainability and access demands.</p>
      <p class="body-copy">From single devices to complex integrated systems, each project is unique to you and your business and is given due care and attention to ensure that you are fully protected with the highest level of security whilst minimising the costs of managing your building infrastructure.</p>
    </div>

    <div class="web-inside">
      <svg viewBox="0 0 10 10"><circle cx="5" cy="5" r="4.3" fill="var(--red)"/><path d="M.7 5h8.6M5 .7c-2.2 2.6-2.2 6 0 8.6M5 .7c2.2 2.6 2.2 6 0 8.6" fill="none" stroke="#000" stroke-width=".7"/></svg>www.northgatetech.co.uk
    </div>
  </section>

</div>
</body>
</html>
```